Für das Kirchenkreismusikfest wird ein Plakat gesucht
Zielgruppe
Wir sind der Kirchenkreis Haldermoor in Niedersachsen. Ich bin der Kirchenkreiskantor (Kirchenmusiker) und veranstalte am 23. Februar ein Kirchenkreismusikfest. Dabei präsentiert sich der Kirchenkreis mit all seinen musikalischen Fassetten. Daran nehmen viele Chöre und musikalische Gruppen aus den Gemeinden im Kirchenkreis teil. Zielgruppe ist das Klient aus den Kirchengemeinden (vornehmlich im Alter von 30-70 m/w), aber für Leute, die nichts mit Kirche am Hut haben, soll das Plakat ebensbo ansprechend sein.
Aufgabenstellung
Wenn möglich, wären die Formate DIN A 3 und DIN A 2 und auch DIN A 4 gut.
Folgender Text soll berücksichtigt werden (kann sich in den nächsten Tagen auch noch mal etwas ändern):
Kirchenkreismusikfest „Mit Stimme, Klang und Freude“
Samstag, 23.2.19 in der St. Veronika-Kirche in Haldermoor
15 Uhr Eröffnung
15.30 bis 19.00 Uhr
19 Uhr Gemeinsamer Abschluss
Dazwischen finden Kurzkonzerte im halbstündigen Abstand statt.
Das Kirchenkreismusikfest wird gestaltet von:
Projektchor „Voices&Bridges“
Bläserchor des Kirchenkreises
Kantorei St. Veronika
Gemeinsames Flötenorchester
Gospelchor Brünnstedt
Organistinnen und Organisten des Kirchenkreises
Gitarrengruppe Ostermarsch
und den Zuschauern selbst
Gesamtleitung: Kirchenkreiskantor Tobias Welkerling
Eintritt frei

```html
<!DOCTYPE html>
<html lang="de">
<head>
<meta charset="utf-8">
<title>Kirchenkreismusikfest – Plakat</title>
<link href="https://fonts.googleapis.com/css2?family=Londrina+Solid:wght@300;400;900&family=Cabin:wght@400;600;700&display=swap" rel="stylesheet">
<style>
  :root{
    --page:#ffffff;
    --paper:#e3c9b8;
    --navy:#0f3a5c;
    --blue:#0b5d8e;
    --sky:#3f9fd6;
    --magenta:#e5238a;
    --white:#ffffff;
    --logo:#8a1f5c;
  }
  *{margin:0;padding:0;box-sizing:border-box}
  html,body{width:1016px;height:1200px;overflow:hidden;background:var(--page)}
  .poster{position:absolute;left:83px;top:20px;width:850px;height:1160px;background:var(--paper);overflow:hidden;font-family:"Cabin",sans-serif;color:var(--navy)}
  .title-disc{position:absolute;left:158px;top:-7px;width:496px;height:496px;border-radius:50%;background:var(--white)}
  .headline{position:absolute;left:0;top:0;width:850px;height:360px;font-family:"Londrina Solid",sans-serif}
  .venue{position:absolute;left:0;width:812px;top:368px;text-align:center;font-size:20px;color:var(--navy)}
  .motto-disc{position:absolute;left:540px;top:383px;width:262px;height:262px;border-radius:50%;background:var(--blue);display:flex;align-items:center;justify-content:center;text-align:center;color:var(--white);font-family:"Londrina Solid",sans-serif;font-size:36px;line-height:1.35;letter-spacing:1.5px}
  .entry{position:absolute;left:66px;top:634px;transform:rotate(-90deg);transform-origin:left top;font-weight:700;font-size:19px;color:var(--navy);white-space:nowrap}
  .schedule{position:absolute;left:124px;top:516px;font-weight:600;font-size:17px;line-height:25px;list-style:none}
  .note{position:absolute;left:124px;top:618px;font-weight:600;font-size:13px}
  .choir-art{position:absolute;left:70px;top:660px;width:686px;height:340px}
  .logo-box{position:absolute;left:0;top:1000px;width:314px;height:115px;background:var(--white);display:flex;align-items:center;justify-content:center;gap:10px}
  .logo-box .mark{width:12px;height:12px;background:var(--logo)}
  .logo-box .name{font-size:15px;font-weight:600;color:var(--logo)}
  .credits{position:absolute;left:378px;top:1018px;width:400px;font-size:9.6px;line-height:13px;color:var(--navy)}
  .credits p+p{margin-top:8px}
</style>
</head>
<body>
<main class="poster">
  <div class="title-disc"></div>
  <svg class="headline" viewBox="0 0 850 360" aria-label="Kirchenkreis Musikfest, Samstag, 23. Feb. 2019">
    <text x="127" y="184" font-size="92" font-weight="900" fill="var(--navy)" textLength="589" lengthAdjust="spacingAndGlyphs">KIRCHENKREIS</text>
    <text x="127" y="278" font-size="110" font-weight="400" fill="var(--blue)" textLength="325" lengthAdjust="spacingAndGlyphs">MUSIK</text>
    <text x="466" y="278" font-size="110" font-weight="900" fill="var(--magenta)" textLength="250" lengthAdjust="spacingAndGlyphs">FEST</text>
    <text x="127" y="343" font-size="56" font-weight="900" fill="var(--navy)" textLength="589" lengthAdjust="spacingAndGlyphs">SAMSTAG, 23.FEB.2019</text>
  </svg>
  <p class="venue">in der St. Veronika-Kirche in Haldermoor</p>
  <div class="motto-disc"><p>MIT STIMME,<br>KLANG UND<br>FREUDE</p></div>
  <p class="entry">Eintritt frei</p>
  <ul class="schedule">
    <li>15 Uhr Eröffnung</li>
    <li>15.30 bis 19.00 Uhr</li>
    <li>19 Uhr Gemeinsamer Abschluss</li>
  </ul>
  <p class="note">Dazwischen finden Kurzkonzerte im halbstündigen Abstand statt.</p>
  <svg class="choir-art" role="img" aria-label="Illustration: singender Chor mit Notenmappen" viewBox="0 0 686 340" preserveAspectRatio="none">
    <defs>
      <linearGradient id="choirTones" x1="0" y1="0" x2="0" y2="1">
        <stop offset="0" stop-color="#1b6fa8"/>
        <stop offset="0.55" stop-color="#3f9fd6"/>
        <stop offset="1" stop-color="#0f3a5c"/>
      </linearGradient>
    </defs>
    <rect width="686" height="340" rx="6" fill="url(#choirTones)"/>
  </svg>
  <div class="logo-box">
    <span class="mark"></span>
    <span class="name">Kirchenkreis Haldermoor</span>
  </div>
  <div class="credits">
    <p>Das Kirchenkreismusikfest wird gestaltet von:</p>
    <p>Projektchor „Voices&amp;Bridges“, Bläserchor des Kirchenkreises, Kantorei St. Veronika, Gemeinsames Flötenorchester, Gospelchor Brünnstedt, Organistinnen und Organisten des Kirchenkreises, Gitarrengruppe Ostermarsch und den Zuschauern selbst</p>
    <p>Gesamtleitung: Kirchenkreiskantor Tobias Welkerling</p>
  </div>
</main>
</body>
</html>
```